Lantern Co. Supplement General Packaging Design

I am looking for a design template to design all of my various supplements and other products around. Meaning that this design should be able to just be able to change around words, up to a few small images, and text to suit my other various products.

The brand name is Lantern Co. and the slogan is: Grit Is Earned
This is For an Apple Cider Vinegar Gummy, and include these top three things: Vegan, Gluten Free, Non-GMO somewhere in the design.

I want the design to have a luxurious feel. With some kind of design element where the logo is sort of the secondary aspect of the design.

Target Market(s)

Men age 24-45

Industry/Entity Type

Supplement

Requirements
Must have
• MUST HAVE A "vintage" LOOK AND FEEL. MUST HAVE ANOTHER design element besides the logo. (Something Vintage) MUST USE THE PROVIDED TEMPLATE A PDF IN THE FILES BELOW LABELED " TEMPLATE" and the LOGO PROVIDED under "Lantern Co. 2" OR "lantern co.3" whichever is better suited for the design. Bold design. Another color besides black to stand out. Use the lantern co logo which is below in the provided images. The design should go around the logo and fit the same aesthetic. The rest are for inspiration, what I like.

```html
<!DOCTYPE html>
<html lang="en">
<head>
<meta charset="utf-8">
<title>Lantern Co. Apple Cider Vinegar Gummy Label</title>
<link href="https://fonts.googleapis.com/css2?family=Bebas+Neue&family=Archivo+Black&display=swap" rel="stylesheet">
<style>
  :root{
    --red:#d9202a;
    --black:#0b0b0b;
    --white:#ffffff;
    --page:#7d7d7d;
    --ink:#111111;
  }
  html,body{margin:0;padding:0;overflow:hidden}
  body{width:1200px;height:1122px;background:var(--page);position:relative;font-family:Arial,Helvetica,sans-serif}
  .label{position:absolute;left:20px;top:415px;width:1352px;height:340px;transform:scale(0.858);transform-origin:0 0;background:var(--red);box-shadow:6px 6px 8px rgba(0,0,0,.35);color:var(--white)}
  .barcode-zone{position:absolute;left:0;top:0;width:70px;height:340px;background:var(--white)}
  .barcode-zone span{position:absolute;left:-65px;top:158px;width:200px;text-align:center;color:var(--ink);font-size:15px;transform:rotate(90deg)}
  .directions{position:absolute;left:85px;top:18px;width:277px;font-size:10.5px;line-height:12.6px}
  .directions p{margin:0 0 11px;text-align:justify}
  .disclaimer{border:1px solid var(--white);padding:5px 8px;margin:0 0 10px}
  .maker-box{background:var(--white);color:var(--ink);border:1px solid var(--ink);height:36px;line-height:36px;text-align:center;font-size:11px;margin-top:6px}
  .panel{position:absolute;left:0;top:0}
  .ribbon-badge{position:absolute;width:42px;height:42px;border-radius:50%;background:var(--white);border:2px solid var(--red);box-shadow:0 0 0 2px var(--white);color:var(--ink);font-size:7.5px;font-weight:bold;line-height:9px;display:flex;align-items:center;justify-content:center;text-align:center}
  .claim-icon{position:absolute;left:826px;width:34px;height:34px;border-radius:50%;background:var(--white)}
  .claim-text{position:absolute;left:810px;width:66px;text-align:center;font-size:9px;font-weight:bold}
  .brand-name{position:absolute;left:520px;width:310px;top:80px;text-align:center;font-family:'Bebas Neue',sans-serif;font-size:44px;letter-spacing:2px}
  .slogan{position:absolute;left:520px;width:310px;top:142px;text-align:center;font-family:'Bebas Neue',sans-serif;font-size:50px;color:var(--red);letter-spacing:.5px}
  .product-name{position:absolute;left:400px;width:550px;top:238px;text-align:center;font-family:'Bebas Neue',sans-serif;font-size:48px;line-height:48px;transform:scaleY(1.1)}
  .product-type{position:absolute;left:400px;width:550px;top:298px;text-align:center;font-weight:bold;font-size:15px;letter-spacing:.5px}
  .facts{position:absolute;left:1007px;top:25px;width:266px;height:286px;border:2px solid var(--white);padding:0 4px;box-sizing:border-box;font-size:10px}
  .facts h2{margin:2px 0 0;font-family:'Archivo Black',sans-serif;font-weight:400;font-size:21px;letter-spacing:.5px;border-bottom:1px solid var(--white);padding-bottom:1px}
  .facts .serving{font-weight:bold;font-size:10.5px;line-height:13px;padding-bottom:4px;border-bottom:5px solid var(--white)}
  .facts .head{text-align:right;font-weight:bold;padding:4px 0 2px;border-bottom:3px solid var(--white)}
  .row{display:grid;grid-template-columns:1fr 62px 30px;border-bottom:1px solid var(--white);line-height:12.5px}
  .row span:nth-child(n+2){text-align:right}
  .row.indent span:first-child{padding-left:10px}
  .row.indent2 span:first-child{padding-left:16px}
  .row.end{border-bottom:4px solid var(--white)}
  .facts .notes{padding-top:4px;line-height:12px}
  .ingredients{position:absolute;left:1161px;top:136px;width:294px;height:48px;transform:rotate(-90deg);font-size:9.8px;line-height:12px}
</style>
</head>
<body>
  <section class="label" aria-label="Lantern Co. Apple Cider Vinegar Gummy label">
    <div class="barcode-zone"><span>Bar-Code Zone</span></div>

    <div class="directions">
      <p><b>Suggested Use:</b> Take one (1) gummy daily or as directed by a healthcare professional.</p>
      <p><b>Caution:</b> If you are pregnant, nursing, taking any medications or have any medical condition, consult your doctor before use. Discontinue use and consult your doctor if any adverse reactions occur.</p>
      <p>KEEP OUT OF REACH OF CHILDREN. STORE AT ROOM TEMPERATURE.</p>
      <p>ALLERGEN WARNING: This product contains tree nuts (coconut).</p>
      <p class="disclaimer">†These statements have not been evaluated by the FDA. This product is not intended to diagnose, cure, treat or prevent any disease.</p>
      <p style="margin:0">Manufactured for:</p>
      <div class="maker-box">Manufactured for Zone</div>
    </div>

    <svg class="panel" width="1352" height="340" viewBox="0 0 1352 340">
      <path d="M410 0 H940 C985 40 990 150 920 212 H440 C365 150 370 40 410 0 Z" fill="#0b0b0b"/>
      <rect x="440" y="218" width="482" height="4" fill="#0b0b0b"/>
      <path d="M475 0 H533 V190 L504 212 L475 190 Z" fill="#d9202a"/>
      <path d="M815 0 H870 V190 L842 212 L815 190 Z" fill="#d9202a"/>
    </svg>

    <div class="ribbon-badge" style="left:483px;top:25px">PECTIN<br>BASED</div>
    <div class="ribbon-badge" style="left:483px;top:75px">Beet Root<br>40 mcg</div>
    <div class="ribbon-badge" style="left:483px;top:128px">Cider<br>500 mg</div>

    <div class="claim-icon" style="top:22px"></div>
    <div class="claim-text" style="top:61px">Vegan</div>
    <div class="claim-icon" style="top:74px"></div>
    <div class="claim-text" style="top:113px">Gluten free</div>
    <div class="claim-icon" style="top:128px"></div>
    <div class="claim-text" style="top:170px">Non-GMO</div>

    <div class="brand-name">Lantern Co.</div>
    <div class="slogan">Grit Is Earned</div>
    <div class="product-name">Apple Cider Vinegar Gummy</div>
    <div class="product-type">DIETARY SUPPLEMENT</div>

    <div class="facts">
      <h2>SUPPLEMENT FACTS</h2>
      <div class="serving">Serving Size: &nbsp;1 Gummy<br>Servings Per Container: 60</div>
      <div class="head">Amount Per Serving &nbsp;% DV</div>
      <div class="row"><span>Calories</span><span>10</span><span></span></div>
      <div class="row"><span>Total Carbohydrates</span><span>3 g</span><span>&lt;1%</span></div>
      <div class="row indent"><span>Total Sugars</span><span>2 g</span><span>**</span></div>
      <div class="row indent2"><span>Includes 2 g Added Sugars</span><span></span><span>4%</span></div>
      <div class="row"><span>Vitamin B-6 (as Pyridoxine HCl)</span><span>0.5 mg</span><span>29%</span></div>
      <div class="row"><span>Folate (120 mcg Folic Acid)</span><span>200 mcg DFE</span><span>50%</span></div>
      <div class="row"><span>Vitamin B-12 (as Cyanocobalamin)</span><span>1.2 mcg</span><span>50%</span></div>
      <div class="row"><span>Iodine (as Potassium Iodide)</span><span>50 mcg</span><span>33%</span></div>
      <div class="row"><span>Apple Cider Vinegar Powder (fruit)<br>(providing 5% total acid)</span><span>500 mg</span><span>**</span></div>
      <div class="row"><span>Pomegranate Juice Powder</span><span>40 mcg</span><span>**</span></div>
      <div class="row end"><span>Beet Root Juice Powder</span><span>40 mcg</span><span>**</span></div>
      <div class="notes">* % Daily Value Based on 2,000 Calorie Diet<br>** Daily Value Not Established</div>
    </div>

    <div class="ingredients"><b>Other Ingredients:</b> Glucose Syrup, Sugar, Glucose, Pectin, Sodium Citrate, Citric Acid, Natural Apple Flavor, Vegetable Oil, Liquid Apple Cider Vinegar, Purple carrot Juice Concentrate and Beta Carotene.</div>
  </section>
</body>
</html>
```